Modern Verdell Tree Care Website

I need a website for a full service Tree Care company. The company provides tree pruning, tree removal, tree preservation, emergency services, stump grinding, and emergency tree services.

Target Market(s)

Customers that need tree services

Industry/Entity Type

Landscaping, Tree Services

Coding

Coded - Design and coding required

Number of Pages Required

5+ page

Font styles to use
Sans Serif

Requirements
Must have
• Good clean design that showcases the services the company provides.
Nice to have
• Services page; contact form, blog, home page, about page

```html
<!DOCTYPE html>
<html lang="en">
<head>
<meta charset="utf-8">
<title>Verdell Tree Care</title>
<link href="https://fonts.googleapis.com/css2?family=Syncopate:wght@700&family=Lato:wght@400;700&family=Sarabun:wght@400;500;600&family=Montserrat:wght@700&family=Roboto+Condensed:wght@700&display=swap" rel="stylesheet">
<style>
:root{
  --slate:#5f6b72;
  --slate-dark:#4f5a60;
  --ink:#222;
  --green:#7dbb3a;
  --green-deep:#6a9a45;
  --orange:#f7a534;
  --tan:#c49665;
  --mist:#dfe3e4;
  --panel:#f3f6ea;
  --white:#fff;
}
*{margin:0;padding:0;box-sizing:border-box}
html,body{width:1200px;height:3736px;overflow:hidden;background:var(--white);font-family:'Lato',sans-serif;color:var(--ink)}
.page{position:relative;width:1200px;height:3736px;overflow:hidden}
.abs{position:absolute}
.display{font-family:'Syncopate',sans-serif;font-weight:700;text-transform:uppercase}
.topbar{left:0;top:0;width:1200px;height:42px;background:var(--slate);color:#fff;font-size:14px;display:flex;align-items:center;justify-content:center}
.header{left:0;top:42px;width:1200px;height:86px;background:#fff}
.brand{display:flex;align-items:center;gap:12px;font-family:'Lato',sans-serif;font-weight:700;color:var(--slate);font-size:30px}
.brand .mark{width:40px;height:40px;background:var(--green)}
.nav{right:100px;top:0;height:86px;display:flex;align-items:center;gap:32px;font-family:'Syncopate',sans-serif;font-weight:700;font-size:14px;color:var(--slate)}
.nav .cta{background:var(--orange);color:#fff;padding:16px 34px 16px 20px;clip-path:polygon(0 0,88% 0,100% 100%,0 100%)}
.hero{left:0;top:128px;width:1200px;height:660px;background:linear-gradient(160deg,#3e5a2e,#5c7440 45%,#2f3f24)}
.hero-title{left:98px;top:300px;font-size:50px;line-height:66px;color:#fff;letter-spacing:1px}
.hero-sub{left:98px;top:442px;color:#fff;font-size:19px;line-height:38px}
.btn-green{background:var(--green);color:#fff;font-family:'Syncopate',sans-serif;font-weight:700;font-size:14px;display:flex;align-items:center;padding-left:20px;clip-path:polygon(0 0,84% 0,100% 100%,0 100%)}
.arrow{width:30px;height:30px}
.section-title{width:1200px;text-align:center;font-size:30px;color:var(--slate);letter-spacing:1px}
.card{top:902px;width:208px;height:198px;border:1.5px solid var(--slate);border-radius:6px;background:#fff;text-align:center;font-family:'Sarabun',sans-serif;font-weight:500;font-size:21px;line-height:31px;color:var(--ink)}
.card svg{display:block;margin:28px auto 14px}
.who-img{left:98px;top:1382px;width:489px;height:411px;background:var(--green-deep);padding:14px}
.who-img div{width:100%;height:100%;background:linear-gradient(135deg,#2f5a24,#5e8c3a 45%,#a0a7a8 65%,#3f6b2a)}
.who-title{left:645px;top:1392px;font-size:29px;color:#fff}
.who-text{left:645px;top:1450px;width:455px;color:#fff;font-size:14.5px;line-height:27.5px}
.svc-img{top:2103px;width:233px;height:255px}
.svc-label{top:2382px;width:233px;text-align:center;font-family:'Sarabun',sans-serif;font-weight:600;font-size:19px}
.contact-title{left:98px;top:2735px;font-family:'Montserrat',sans-serif;font-size:38px;color:#fff}
.contact-rule{left:98px;top:2798px;width:215px;height:3px;background:#fff}
.contact-copy{left:98px;top:2818px;width:460px;color:#fff;font-size:15.5px;line-height:24px;font-family:'Lato',sans-serif}
.info{color:#fff;font-family:'Lato',sans-serif}
.info small{display:block;font-size:15px;opacity:.75}
.info span{font-size:17px;line-height:24px}
.form{left:586px;top:2665px;width:542px;height:490px;background:var(--panel);padding:26px 30px}
.form label{position:absolute;font-size:13.5px;color:#222}
.field{position:absolute;height:42px;border:1px solid var(--slate);background:#f7f9f0;font-size:13px;color:#777;padding:13px 18px}
.send{position:absolute;left:30px;top:440px;width:482px;height:46px;background:var(--slate);color:#fff;font-family:'Roboto Condensed',sans-serif;font-size:15px;display:flex;align-items:center;justify-content:center;border-radius:2px}
.foot-nav{left:0;top:3524px;width:1200px;display:flex;justify-content:center;gap:40px;font-size:15px;color:#222}
.foot-item{top:3583px;display:flex;align-items:center;gap:22px;font-size:16px}
.foot-item .ico{width:48px;height:48px;background:var(--green);display:flex;align-items:center;justify-content:center}
.copyright{left:0;top:3672px;width:1200px;text-align:center;font-size:14px}
</style>
</head>
<body>
<div class="page">

  <div class="abs topbar">Call&nbsp;<b>HALLORAN</b>&nbsp;for a Free Estimate</div>

  <header class="abs header">
    <div class="abs brand" style="left:98px;top:22px"><span class="mark"></span>Verdell Tree Care</div>
    <nav class="abs nav"><span>Home</span><span>About</span><span>Services</span><span>Blog</span><span class="cta">Contact</span></nav>
  </header>

  <section class="abs hero" role="img" aria-label="Arborist in safety gear cutting a log with a chainsaw in a pine forest"></section>
  <svg class="abs" style="left:0;top:660px" width="1200" height="130" viewBox="0 0 1200 130">
    <polygon points="970,22 1200,0 1200,110" fill="var(--tan)"/>
    <polygon points="0,130 970,22 1200,110 1200,130" fill="#fff"/>
  </svg>
  <h1 class="abs display hero-title">Welcome to<br>Verdell</h1>
  <p class="abs hero-sub">Call <b>VERDELL</b> for All Your Tree Care Needs<br>Serving Lafayette and surrounding areas</p>
  <div class="abs btn-green" style="left:98px;top:530px;width:195px;height:47px">Get Started</div>
  <svg class="abs arrow" style="left:34px;top:410px" viewBox="0 0 30 30"><circle cx="15" cy="15" r="13" fill="none" stroke="#fff" stroke-width="1.5"/><path d="M17 9l-6 6 6 6" fill="none" stroke="#fff" stroke-width="1.5"/></svg>
  <svg class="abs arrow" style="left:1135px;top:410px" viewBox="0 0 30 30"><circle cx="15" cy="15" r="13" fill="none" stroke="#fff" stroke-width="1.5"/><path d="M13 9l6 6-6 6" fill="none" stroke="#fff" stroke-width="1.5"/></svg>

  <h2 class="abs display section-title" style="left:0;top:828px">Why Choose Us?</h2>
  <svg class="abs arrow" style="left:50px;top:986px" viewBox="0 0 30 30"><circle cx="15" cy="15" r="13" fill="none" stroke="#999" stroke-width="1.5"/><path d="M17 9l-6 6 6 6" fill="none" stroke="#999" stroke-width="1.5"/></svg>
  <svg class="abs arrow" style="left:1121px;top:986px" viewBox="0 0 30 30"><circle cx="15" cy="15" r="13" fill="none" stroke="#222" stroke-width="1.5"/><path d="M13 9l6 6-6 6" fill="none" stroke="#222" stroke-width="1.5"/></svg>

  <div class="abs card" style="left:124px">
    <svg width="76" height="70" viewBox="0 0 76 70" fill="none" stroke="var(--slate)" stroke-width="2"><rect x="8" y="24" width="6" height="18"/><rect x="18" y="16" width="6" height="26"/><path d="M4 20 28 4"/><path d="M48 22l18 6v14c0 12-8 20-18 24-10-4-18-12-18-24V28z"/><circle cx="48" cy="44" r="10" stroke="var(--green)"/><path d="M43 44l4 4 7-8" stroke="var(--green)"/></svg>
    Licensed and<br>Insured
  </div>
  <div class="abs card" style="left:371px">
    <svg width="64" height="70" viewBox="0 0 64 70" fill="none" stroke="var(--slate)" stroke-width="2"><path d="M6 4h34l10 10v52H6z"/><path d="M14 20h24M14 30h24M14 40h16"/><circle cx="46" cy="46" r="8" stroke="var(--green)"/><path d="M42 54l-2 12 6-4 6 4-2-12" stroke="var(--green)"/></svg>
    Free<br>Estimates
  </div>
  <div class="abs card" style="left:619px">
    <svg width="64" height="70" viewBox="0 0 64 70" fill="none" stroke="var(--slate)" stroke-width="2"><path d="M14 6h40v48a10 10 0 0 1-10 10H8V54h36"/><path d="M14 6a6 6 0 0 0-6 6v6h6"/><path d="M34 16l10 4v8c0 6-4 10-10 12-6-2-10-6-10-12v-8z" stroke="var(--green)"/><path d="M30 28l3 3 5-6" stroke="var(--green)"/></svg>
    Licensed Arborist<br>on Staff
  </div>
  <div class="abs card" style="left:867px">
    <svg width="70" height="70" viewBox="0 0 70 70" fill="none" stroke="var(--slate)" stroke-width="2"><circle cx="35" cy="35" r="26" stroke-dasharray="8 4"/><circle cx="35" cy="35" r="18"/><path d="M24 36l6-6 5 4 5-4 6 6-8 7z" stroke="var(--green)"/></svg>
    Professional<br>Work
  </div>

  <svg class="abs" style="left:0;top:1160px" width="1200" height="840" viewBox="0 0 1200 840">
    <polygon points="0,0 265,123 0,145" fill="var(--orange)"/>
    <polygon points="0,145 1200,58 1200,665 0,826" fill="var(--slate)"/>
    <polygon points="0,826 1200,665 1200,690 0,840" fill="var(--mist)"/>
  </svg>
  <div class="abs who-img"><div role="img" aria-label="Red-handled pruning shears cutting a mossy branch"></div></div>
  <h2 class="abs display who-title">Who We Are</h2>
  <div class="abs who-text">
    <p>At Verdell Tree Care, we are more than just a tree service company, we are stewards of our beautiful trees. With a passion deeply rooted in arboriculture, we embark on a mission to promote the health, beauty, and safety of your trees and landscapes.</p>
    <p style="margin-top:27px">Whether it's expert tree trimming to enhance aesthetics, meticulous tree removal to mitigate hazards, or comprehensive tree health assessments to ensure safety, we approach each task with unwavering dedication and attention to detail.</p>
  </div>
  <div class="abs btn-green" style="left:645px;top:1730px;width:194px;height:46px">Learn More</div>

  <h2 class="abs display section-title" style="left:0;top:2028px">Our Services</h2>
  <svg class="abs arrow" style="left:33px;top:2215px" viewBox="0 0 30 30"><circle cx="15" cy="15" r="13" fill="none" stroke="#999" stroke-width="1.5"/><path d="M17 9l-6 6 6 6" fill="none" stroke="#999" stroke-width="1.5"/></svg>
  <svg class="abs arrow" style="left:1135px;top:2215px" viewBox="0 0 30 30"><circle cx="15" cy="15" r="13" fill="none" stroke="#222" stroke-width="1.5"/><path d="M13 9l6 6-6 6" fill="none" stroke="#222" stroke-width="1.5"/></svg>
  <div class="abs svc-img" style="left:98px;background:linear-gradient(180deg,#c9dbe8,#8fb06a 55%,#3f6a2c)" role="img" aria-label="Worker trimming a hedge with a pole pruner"></div>
  <div class="abs svc-img" style="left:355px;background:linear-gradient(135deg,#3d5a2c,#6b5a44 50%,#2e3b26)" role="img" aria-label="Arborist cutting a tree trunk with a chainsaw"></div>
  <div class="abs svc-img" style="left:612px;background:linear-gradient(180deg,#9fc46a,#4f7a30 60%,#b8ad98)" role="img" aria-label="Tree-lined garden path"></div>
  <div class="abs svc-img" style="left:868px;background:linear-gradient(180deg,#5f7a4a,#7a4e2e 50%,#4a3322)" role="img" aria-label="Old tree stump before grinding"></div>
  <div class="abs svc-label" style="left:98px">Tree Pruning</div>
  <div class="abs svc-label" style="left:355px">Tree Removal</div>
  <div class="abs svc-label" style="left:612px">Tree Preservation</div>
  <div class="abs svc-label" style="left:868px">Stump Grinding</div>

  <svg class="abs" style="left:0;top:2430px" width="1200" height="960" viewBox="0 0 1200 960">
    <defs><linearGradient id="grass" x1="0" y1="0" x2="1" y2="1"><stop offset="0" stop-color="#8cc43f"/><stop offset="1" stop-color="#72ad34"/></linearGradient></defs>
    <polygon points="0,55 1200,155 1200,920 0,770" fill="url(#grass)"/>
    <polygon points="1200,0 1200,155 1000,140" fill="var(--tan)"/>
    <polygon points="0,770 1200,920 1200,955 0,815" fill="#e8f2dc"/>
  </svg>
  <h2 class="abs contact-title">CONTACT US</h2>
  <div class="abs contact-rule"></div>
  <p class="abs contact-copy">Join us on this journey toward financial freedom. Let Kestrel Capital Management be your guide. Illuminating the path to a brighter, more secure future.</p>

  <svg class="abs" style="left:100px;top:2945px" width="24" height="18" viewBox="0 0 24 18" fill="none" stroke="#fff" stroke-width="1.8"><rect x="1" y="1" width="22" height="16"/><path d="M1 1l11 9 11-9"/></svg>
  <div class="abs info" style="left:134px;top:2930px"><small>Email</small><span>info@verdelltreecare.com</span></div>
  <svg class="abs" style="left:380px;top:2942px" width="22" height="22" viewBox="0 0 24 24" fill="#fff"><path d="M6.6 10.8a15 15 0 0 0 6.6 6.6l2.2-2.2c.3-.3.7-.4 1-.2 1.1.4 2.3.6 3.6.6.6 0 1 .4 1 1V20c0 .6-.4 1-1 1A17 17 0 0 1 3 4c0-.6.4-1 1-1h3.5c.6 0 1 .4 1 1 0 1.3.2 2.5.6 3.6.1.3 0 .7-.2 1z"/></svg>
  <div class="abs info" style="left:416px;top:2932px"><small>Call Us</small><span>(337) 555-0142</span></div>
  <svg class="abs" style="left:102px;top:3040px" width="18" height="24" viewBox="0 0 18 24" fill="#fff"><path d="M9 0a9 9 0 0 0-9 9c0 7 9 15 9 15s9-8 9-15a9 9 0 0 0-9-9zm0 12a3 3 0 1 1 0-6 3 3 0 0 1 0 6z"/></svg>
  <div class="abs info" style="left:134px;top:3027px"><small>Address</small><span>Verdell Tree Care, Maple Row,<br>LA 70599</span></div>
  <div class="abs info" style="left:416px;top:3030px"><small>Social</small></div>
  <div class="abs" style="left:420px;top:3062px;display:flex;gap:16px">
    <span style="width:16px;height:16px;border-radius:50%;border:2px solid #fff"></span>
    <span style="width:16px;height:16px;border-radius:50%;border:2px solid #fff"></span>
    <span style="width:16px;height:16px;border-radius:50%;border:2px solid #fff"></span>
    <span style="width:16px;height:16px;border-radius:50%;border:2px solid #fff"></span>
  </div>

  <form class="abs form">
    <label style="left:30px;top:26px">First Name</label>
    <div class="field" style="left:30px;top:48px;width:234px">First Name</div>
    <label style="left:278px;top:26px">Last Name</label>
    <div class="field" style="left:278px;top:48px;width:234px">Last Name</div>
    <label style="left:30px;top:108px">Email</label>
    <div class="field" style="left:30px;top:130px;width:482px">Email</div>
    <label style="left:28px;top:190px">Phone Number</label>
    <div class="field" style="left:30px;top:211px;width:482px">Phone Number</div>
    <label style="left:28px;top:270px">Message</label>
    <div class="field" style="left:30px;top:291px;width:482px;height:132px"></div>
    <div class="send">SEND MESSAGE</div>
  </form>

  <div class="abs brand" style="left:0;top:3430px;width:1200px;justify-content:center;font-size:36px"><span class="mark" style="width:46px;height:46px"></span>Verdell Tree Care</div>
  <nav class="abs foot-nav"><span>HOME</span><span>ABOUT</span><span>SERVICES</span><span>BLOG</span><span>CONTACT</span></nav>
  <div class="abs foot-item" style="left:146px"><span class="ico"><svg width="24" height="18" viewBox="0 0 24 18" fill="none" stroke="#fff" stroke-width="2"><rect x="1" y="1" width="22" height="16"/><path d="M1 1l11 9 11-9"/></svg></span>info@verdelltreecare.com</div>
  <div class="abs foot-item" style="left:497px;font-size:14px"><span class="ico"><svg width="18" height="24" viewBox="0 0 18 24" fill="#fff"><path d="M9 0a9 9 0 0 0-9 9c0 7 9 15 9 15s9-8 9-15a9 9 0 0 0-9-9zm0 12a3 3 0 1 1 0-6 3 3 0 0 1 0 6z"/></svg></span>Verdell Tree Care, Maple Row, LA</div>
  <div class="abs foot-item" style="left:855px;font-size:17px"><span class="ico"><svg width="22" height="22" viewBox="0 0 24 24" fill="#fff"><path d="M6.6 10.8a15 15 0 0 0 6.6 6.6l2.2-2.2c.3-.3.7-.4 1-.2 1.1.4 2.3.6 3.6.6.6 0 1 .4 1 1V20c0 .6-.4 1-1 1A17 17 0 0 1 3 4c0-.6.4-1 1-1h3.5c.6 0 1 .4 1 1 0 1.3.2 2.5.6 3.6.1.3 0 .7-.2 1z"/></svg></span>(318) 555-0187</div>
  <p class="abs copyright">Copyrights@2024.Verdell Tree Care..All Rights Reserved</p>

</div>
</body>
</html>
```